Sonic Vale

Rebrand current website and move it to SonicVale.com. Looking for a professional, eye catching, top 10 in World type website. My current website is: https://madebytorven.sitepadhub.com/sonicvale
I would like it moved to sonicvale.com.

```html
<!DOCTYPE html>
<html lang="en">
<head>
<meta charset="utf-8">
<title>Sonic Vale</title>
<link href="https://fonts.googleapis.com/css2?family=Heebo:wght@400;500;700&family=Roboto:wght@400;500;700&family=Marcellus+SC&display=swap" rel="stylesheet">
<style>
:root{
  --ink:#141414;
  --bar:#1b1b1b;
  --panel:#222;
  --card:#3a3a3a;
  --blue:#1348e0;
  --blue-bright:#1f5bff;
  --text:#fff;
  --muted:#cfcfcf;
  --row:#2c2c2c;
  --row-alt:#3b3b3b;
}
*{box-sizing:border-box;margin:0;padding:0}
html,body{width:1200px;height:4209px;overflow:hidden}
body{background:var(--ink);color:var(--text);font-family:"Roboto",Arial,sans-serif;position:relative}
.abs{position:absolute}
section,header,footer{position:absolute;left:0;width:1200px;overflow:hidden}

/* top bar */
.topbar{top:0;height:56px;background:var(--bar);font-size:14px}
.topbar .follow{left:111px;top:19px;display:flex;gap:12px;align-items:center}
.dot-icon{width:11px;height:11px;border-radius:50%;background:#fff;display:inline-block}
.topbar .right{right:111px;top:18px;display:flex;gap:16px;align-items:center}

/* hero */
.hero{top:56px;height:562px;background:linear-gradient(100deg,#1a1a1a 0%,#2e2e2e 45%,#5a5a5a 75%,#2b2b2b 100%)}
.hero-photo{right:0;top:0;width:520px;height:562px;background:radial-gradient(ellipse at 60% 45%,#bdbdbd 0%,#6d6d6d 30%,#2c2c2c 70%,transparent 100%)}
.logo{left:111px;top:16px;font-family:"Marcellus SC",serif;font-size:32px;color:#fff}
.nav{right:111px;top:31px;display:flex;gap:60px;font-size:14px;font-weight:400}
.hero h1{left:111px;top:165px;width:560px;font-family:"Heebo",sans-serif;font-weight:700;font-size:50px;line-height:74px}
.hero p{left:113px;top:318px;width:440px;font-size:14px;line-height:30px;color:#eee}
.btn-outline{left:111px;top:396px;width:152px;height:41px;border:2px solid #fff;border-radius:21px;font-size:14px;font-weight:700;display:flex;align-items:center;justify-content:center}
.dots{left:526px;top:498px;display:flex;gap:6px}
.dots span{width:12px;height:12px;border-radius:50%;background:#fff}
.dots span.off{background:transparent;border:2px solid #fff}

/* headings with blue strike */
.strike{font-family:"Heebo",sans-serif;font-weight:700;position:absolute;white-space:nowrap;isolation:isolate}
.strike::before{content:"";position:absolute;left:-16px;right:-16px;top:55%;height:3px;background:var(--blue);z-index:-1}
.strike span{position:relative}

/* bio */
.bio{top:618px;height:801px;background:radial-gradient(ellipse at 70% 40%,#2a2a2a,#121212 75%)}
.bio-frame{left:111px;top:85px;width:417px;height:561px;border:4px solid var(--blue);border-radius:4px}
.bio-photo{left:185px;top:147px;width:417px;height:563px;background:linear-gradient(160deg,#0d0d0d 0%,#0d0d0d 30%,#7a7a7a 55%,#2a2a2a 80%,#111 100%)}
.bio p{left:636px;top:318px;width:450px;font-size:15px;line-height:30px;color:#eee}
.bio .sign{left:640px;top:530px;color:var(--blue-bright);font-size:19px;font-weight:700}

/* album */
.album{top:1419px;height:837px;background:linear-gradient(180deg,#262626,#1c1c1c)}
.album h2{left:0;width:1200px;top:75px;text-align:center;font-size:32px}
.album h2 .strike{position:relative;display:inline-block}
.alb-frame{left:114px;top:165px;width:277px;height:272px;border:4px solid var(--blue);border-radius:4px}
.disc{left:302px;top:208px;width:252px;height:252px;border-radius:50%;background:radial-gradient(circle,#555 0 10%,#e8e8e8 11% 30%,#fff 31% 100%)}
.alb-photo{left:147px;top:198px;width:281px;height:275px;background:linear-gradient(135deg,#6b4a33,#c9966b 45%,#8a5a3a 75%,#3b2a20)}
.album h3{left:111px;top:508px;font-size:24px;font-weight:500}
.album .copy{left:111px;top:561px;width:290px;font-size:15px;line-height:30px;color:#eee}
.btn-blue{background:var(--blue);border-radius:21px;font-size:15px;display:flex;align-items:center;justify-content:center;color:#fff}
.album .btn-blue{left:110px;top:698px;width:160px;height:41px}
.player{left:589px;top:165px;width:500px;height:584px;background:#1d1d1d;border-radius:4px;overflow:hidden}
.player .thumb{left:14px;top:15px;width:111px;height:103px;background:linear-gradient(135deg,#3b5a9a,#9a6b52 60%,#5c4c44)}
.player .play{left:47px;top:47px;width:45px;height:45px;border-radius:50%;background:#fff}
.player .meta{left:136px;top:14px;font-size:15px;line-height:30px;width:130px}
.player .ctrl{left:136px;top:84px;display:flex;gap:20px;align-items:center}
.player .track{left:252px;top:93px;width:116px;height:4px;background:#777}
.player .time{left:425px;top:110px;font-size:13px}
.player .prog{left:0;top:137px;width:500px;height:7px;background:#444}
.playlist{left:0;top:146px;width:490px}
.playlist div{height:44px;display:flex;justify-content:space-between;align-items:center;padding:0 20px 0 22px;font-size:15px;background:var(--row);border-bottom:1px solid #555}
.playlist div span:last-child{font-size:13px}
.playlist div:nth-child(even){background:var(--row-alt)}
.scroll{left:490px;top:146px;width:10px;height:438px;background:#fff}
.scroll::after{content:"";position:absolute;left:2px;top:40px;width:6px;height:40px;background:#333}

/* contact */
.contact{top:2256px;height:746px;background:linear-gradient(135deg,#2a0f52 0%,#4b1e8c 35%,#2c1460 65%,#13082a 100%)}
.contact h2{left:0;width:1200px;top:100px;text-align:center;font-family:"Heebo",sans-serif;font-weight:700;font-size:34px}
.field{width:370px;height:44px;border:1px solid #ccc;border-radius:3px;font-size:15px;padding:14px 14px}
.contact .msg{left:198px;top:366px;width:772px;height:173px}
.contact .btn-blue{left:508px;top:579px;width:103px;height:40px}

/* news */
.news{top:3002px;height:785px;background:#171717}
.news h2{left:0;width:1200px;top:90px;text-align:center;font-size:32px}
.news h2 .strike{position:relative;display:inline-block}
.card{top:178px;width:314px;height:499px;background:var(--card)}
.card .img{left:0;top:0;width:314px;height:221px}
.card .date{left:30px;top:235px;font-size:15px}
.card .cat{right:38px;top:235px;font-size:14px;color:var(--blue)}
.card h4{left:18px;top:272px;width:278px;text-align:center;font-size:18px;font-weight:700;line-height:30px}
.card p{left:18px;top:343px;width:278px;text-align:center;font-size:15px;line-height:30px;color:#eee}
.card .btn-blue{left:78px;top:479px;width:158px;height:41px;font-weight:500;z-index:2}

/* footer */
.footer{top:3787px;height:422px;background:var(--ink)}
.fcol{top:40px;width:330px;text-align:center;font-size:13px;line-height:40px}
.fcol h5{font-size:18px;font-weight:700;position:relative;display:inline-block;line-height:40px;isolation:isolate}
.fcol h5::before{content:"";position:absolute;left:-14px;right:-14px;top:55%;height:2px;background:var(--blue);z-index:-1}
.fcol h5 span{position:relative}
.fcol .sm{color:var(--blue);font-size:11px;line-height:20px}
.news-input{margin:10px auto 0;width:256px;height:40px;border:1px solid #ccc;border-radius:3px;font-size:11px;text-align:left;padding:0 10px;display:flex;justify-content:space-between;align-items:center}
.rule{left:111px;top:285px;width:978px;height:1px;background:#333}
.copyright{left:0;width:1200px;top:306px;text-align:center;font-size:15px}
.socials{left:554px;top:352px;display:flex;gap:9px}
.socials span{width:34px;height:34px;border-radius:50%;background:var(--blue)}
</style>
</head>
<body>

<header class="topbar">
  <div class="abs follow">Follow Us: <span class="dot-icon"></span><span class="dot-icon"></span><span class="dot-icon"></span><span class="dot-icon"></span></div>
  <div class="abs right">Login
    <svg width="18" height="16" viewBox="0 0 18 16" fill="#fff"><path d="M1 4h16l-2 10H3z"/><rect x="5" y="1" width="8" height="3" fill="none" stroke="#fff" stroke-width="1.6"/></svg>
    <svg width="14" height="14" viewBox="0 0 14 14"><circle cx="6" cy="6" r="4.5" fill="none" stroke="#fff" stroke-width="2"/><path d="M9 9l4 4" stroke="#fff" stroke-width="2"/></svg>
  </div>
</header>

<section class="hero">
  <div class="abs hero-photo" role="img" aria-label="Studio condenser microphone with pop filter in black and white"></div>
  <div class="abs logo">Sonic Vale</div>
  <nav class="abs nav"><span>HOME</span><span>ABOUT US</span><span>SERVICES</span><span>TESTIMONIALS</span><span>CONTACT US</span></nav>
  <h1 class="abs">Journey With Torven Ashby</h1>
  <p class="abs">Lorem ipsum dolor sit amet, consectetur adipiscing elit, sed do eiusmod tempor incididunt ut labore et dolore magna</p>
  <div class="abs btn-outline">PLAY MUSIC</div>
  <div class="abs dots"><span></span><span class="off"></span><span></span><span></span></div>
</section>

<section class="bio">
  <div class="abs bio-frame"></div>
  <div class="abs bio-photo" role="img" aria-label="Close-up of a mixing console's faders and knobs"></div>
  <h2 class="strike" style="left:651px;top:235px;font-size:32px"><span>Biography</span></h2>
  <p class="abs">Intricate but gritty music producer who specializes in all phases of music production.A a Certified Audio Engineer and a beat maker of genres(hip hop,trap,edm,R&amp;B etc..)I think it's most important to take pride in quality sound when your involved in any step of the process of creating! Your Music will be professional mixed and mastered to a industry standard.</p>
  <div class="abs sign">Torven Ashby</div>
</section>

<section class="album">
  <h2 class="abs"><span class="strike"><span>Latest Album</span></span></h2>
  <div class="abs alb-frame"></div>
  <div class="abs disc"></div>
  <div class="abs alb-photo" role="img" aria-label="Singer with headphones and acoustic guitar at a studio microphone"></div>
  <h3 class="abs">NIGHT SHIFT (Remastered)</h3>
  <p class="abs copy">Lorem ipsum dolor sit amet, consectetur adipiscing elit, sed do eiusmod tempor incididunt ut labore et dolore magna aliqua. Quis ipsum</p>
  <div class="abs btn-blue">Single $200.00</div>

  <div class="abs player">
    <div class="abs thumb" role="img" aria-label="Track cover art"></div>
    <div class="abs play"><svg width="45" height="45" viewBox="0 0 45 45"><path d="M18 14l13 8.5L18 31z" fill="#1f5bff"/></svg></div>
    <div class="abs meta">Torven &nbsp;Low Tide Sessions</div>
    <div class="abs ctrl">
      <svg width="12" height="12" viewBox="0 0 12 12" fill="#fff"><path d="M11 1v10L2 6z"/></svg>
      <svg width="12" height="12" viewBox="0 0 12 12" fill="#fff"><path d="M1 1v10l10-5z"/></svg>
      <svg width="14" height="12" viewBox="0 0 14 12" fill="#fff"><path d="M1 4h3l4-3v10L4 8H1z"/><path d="M10 3q3 3 0 6" stroke="#fff" fill="none"/></svg>
    </div>
    <div class="abs track"></div>
    <div class="abs time">0:00 &nbsp;/ &nbsp;4:16</div>
    <div class="abs prog"></div>
    <div class="abs playlist">
      <div><span>Low Tide / Torven</span><span>4:16</span></div>
      <div><span>Paper Moon / Torven</span><span>4:16</span></div>
      <div><span>Glass Hours / Torven</span><span>4:16</span></div>
      <div><span>Static Bloom / Torven</span><span>4:16</span></div>
      <div><span>Driftline / Torven</span><span>4:16</span></div>
      <div><span>Neon Rain / Torven</span><span>4:16</span></div>
      <div><span>Back Roads / Torven</span><span>4:16</span></div>
      <div><span>Shore to Shore / Torven</span><span>4:16</span></div>
      <div><span>Slow Orbit / Torven</span><span>4:16</span></div>
      <div><span>Velvet / Torven</span><span>4:16</span></div>
    </div>
    <div class="abs scroll"></div>
  </div>
</section>

<section class="contact" role="img" aria-label="Mixing desk and headphones in purple light">
  <h2 class="abs">Contact Us</h2>
  <div class="abs field" style="left:198px;top:213px">Your Name</div>
  <div class="abs field" style="left:598px;top:213px">Phone</div>
  <div class="abs field" style="left:198px;top:290px">Address</div>
  <div class="abs field" style="left:598px;top:290px">Email</div>
  <div class="abs field msg">Message</div>
  <div class="abs btn-blue">SUBMIT</div>
</section>

<section class="news">
  <h2 class="abs"><span class="strike"><span>Latest News</span></span></h2>

  <article class="abs card" style="left:111px">
    <div class="abs img" role="img" aria-label="Mixing console faders in shallow focus" style="background:linear-gradient(160deg,#3a5a6a,#c9b07a 45%,#2a2a2a)"></div>
    <div class="abs date">Jan 23, 2021</div><div class="abs cat">Music</div>
    <h4 class="abs">5 Things the Artist Needs to Know Before Recording</h4>
    <p class="abs">This is your blog post. Blogs are a great way to connect with your audience and keep them coming back. They can also be a great way to...</p>
    <div class="abs btn-blue">LEARN MORE</div>
  </article>

  <article class="abs card" style="left:441px">
    <div class="abs img" role="img" aria-label="Hands adjusting a studio mixing desk" style="background:linear-gradient(160deg,#6a3a2a,#3a3a3a 45%,#bcbcbc 70%,#222)"></div>
    <div class="abs date">Jan 23, 2021</div><div class="abs cat">Music</div>
    <h4 class="abs">Recording Equipment Must-Haves for Every Studio</h4>
    <p class="abs">This is your blog post. Great looking images make your blog posts more visually compelling for your audience, so choose media that really...</p>
    <div class="abs btn-blue">LEARN MORE</div>
  </article>

  <article class="abs card" style="left:772px">
    <div class="abs img" role="img" aria-label="Studio microphone close-up with blurred lights" style="background:linear-gradient(200deg,#d8d8d8,#6a6a6a 35%,#1a1a1a 80%)"></div>
    <div class="abs date">Jan 23, 2021</div><div class="abs cat">Music</div>
    <h4 class="abs">Sound Check: Recording Tips from the Pros</h4>
    <p class="abs">This is your blog post. To really engage your site visitors we suggest you blog about subjects that are related to your site or business....</p>
    <div class="abs btn-blue">LEARN MORE</div>
  </article>
</section>

<footer class="footer">
  <div class="abs fcol" style="left:80px">
    <h5><span>My Contacts</span></h5>
    <div><svg width="9" height="12" viewBox="0 0 9 12"><path d="M4.5 0a4.5 4.5 0 0 1 4.5 4.5C9 8 4.5 12 4.5 12S0 8 0 4.5A4.5 4.5 0 0 1 4.5 0z" fill="#1f5bff"/></svg> Lorem ipsum dolor sit amet, consectetur</div>
    <div><svg width="11" height="11" viewBox="0 0 11 11"><path d="M2 0l2 3-1 1.5a7 7 0 0 0 3.5 3.5L8 7l3 2-1.5 2A10 10 0 0 1 0 1.5z" fill="#1f5bff"/></svg> 555-210-3374</div>
    <div><svg width="13" height="10" viewBox="0 0 13 10"><rect width="13" height="10" rx="1" fill="#1f5bff"/><path d="M0 1l6.5 5L13 1" stroke="#171717" fill="none"/></svg> madebytorven@mailbox.com</div>
  </div>
  <div class="abs fcol" style="left:425px">
    <h5><span>My Newsletter</span></h5>
    <div style="line-height:26px;margin-top:6px">Lorem ipsum dolor sit amet, consectetur<br>adipiscing elit</div>
    <div class="news-input">Your Email Address <svg width="12" height="9" viewBox="0 0 13 10"><rect width="13" height="10" rx="1" fill="#1f5bff"/></svg></div>
  </div>
  <div class="abs fcol" style="left:775px">
    <h5><span>Recent Posts</span></h5>
    <div style="line-height:26px;margin-top:4px">Recording Equipment Must-Haves for Every Studio</div>
    <div class="sm">Jan 23, 2020</div>
    <div style="line-height:26px;margin-top:14px">Sound Check: Recording Tips from the Pros</div>
    <div class="sm">Jan 23, 2020</div>
  </div>
  <div class="abs rule"></div>
  <div class="abs copyright">©Copyrights 2021 Company Name &nbsp;| &nbsp;&nbsp;All Rights Reserved</div>
  <div class="abs socials"><span></span><span></span><span></span></div>
</footer>

</body>
</html>
```